Veltrano.co - Polar Expeditions Specialists

We need a modern, visually striking business card for Veltrano.co, a company specialized in selling expedition cruises to the most remote regions on Earth, with a focus on the Arctic and Antarctica. The design should instantly communicate that the cardholder is an expert in polar travel. Use clean, premium aesthetics with cool tones like icy blue and white, possibly incorporating polar imagery (ice, glaciers, penguins, etc.)

Attached the logo

Contact Information for Business Card

Feels high-end and trustworthy.. Visually memorable — encourages people to keep it

Colors
0054AA
0677BA
7BADD7
CADEEF
E8F1F8

Requirements
Must have
• ice, glaciers, penguins, montains
Nice to have
• modern, transparente,

```html
<!DOCTYPE html>
<html lang="en">
<head>
<meta charset="utf-8">
<title>Veltrano.co Business Card</title>
<link href="https://fonts.googleapis.com/css2?family=Poppins:wght@400;500;600;700&display=swap" rel="stylesheet">
<style>
  :root {
    --page: #dfe5e6;
    --card: #14132a;
    --brand-blue: #2d7abf;
    --silver: #8c8aa2;
    --white: #ffffff;
  }
  * { margin: 0; padding: 0; box-sizing: border-box; }
  html, body {
    width: 1200px; height: 960px; overflow: hidden;
    background: var(--page);
    font-family: "Poppins", sans-serif;
  }
  .card {
    position: absolute; left: 250px; width: 702px; height: 400px;
    background: var(--card);
    border-bottom: 2px solid var(--brand-blue);
  }
  .card--front { top: 60px; }
  .card--back { top: 501px; }

  .brand-dot {
    position: absolute; border-radius: 50%;
  }
  .card--front .brand-dot {
    left: 302px; top: 96px; width: 90px; height: 90px;
    background: var(--silver);
  }
  .front-name {
    position: absolute; left: 0; width: 100%; top: 214px;
    text-align: center; font-weight: 700; font-size: 60px;
    line-height: 1; color: var(--silver); letter-spacing: -0.5px;
  }
  .front-tagline {
    position: absolute; left: 0; width: 100%; top: 291px;
    text-align: center; font-weight: 600; font-size: 19px;
    color: var(--silver);
  }

  .brand-block {
    position: absolute; left: 0; width: 340px; top: 0; height: 100%;
  }
  .card--back .brand-dot {
    left: 132px; top: 112px; width: 76px; height: 76px;
    background: var(--brand-blue);
  }
  .brand-name {
    position: absolute; left: 0; width: 100%; top: 218px;
    text-align: center; font-weight: 700; font-size: 47px;
    line-height: 1; color: var(--brand-blue); letter-spacing: -0.5px;
  }
  .brand-tagline {
    position: absolute; left: 0; width: 100%; top: 272px;
    text-align: center; font-weight: 600; font-size: 15px;
    color: var(--brand-blue);
  }
  .divider {
    position: absolute; left: 350px; top: 71px; width: 2px; height: 259px;
    background: var(--brand-blue);
  }
  .contact {
    position: absolute; left: 406px; top: 82px; color: var(--white);
  }
  .person-name {
    font-size: 34px; line-height: 1.1; color: var(--brand-blue); font-weight: 400;
    letter-spacing: 0.5px;
  }
  .person-name strong { font-weight: 600; }
  .person-title { font-size: 18px; font-weight: 500; margin-top: 2px; }
  .address { font-size: 18.5px; line-height: 25px; margin-top: 18px; letter-spacing: 0.3px; }
  .details { list-style: none; margin-top: 18px; }
  .details li {
    display: flex; align-items: center; gap: 12px;
    font-size: 19.5px; line-height: 26px; letter-spacing: 0.3px;
  }
  .details svg { width: 17px; height: 17px; flex: none; }
</style>
</head>
<body>
  <section class="card card--front" aria-label="Card front">
    <span class="brand-dot"></span>
    <p class="front-name">Veltrano.co</p>
    <p class="front-tagline">Polar Expeditions Specialists</p>
  </section>

  <section class="card card--back" aria-label="Card back">
    <div class="brand-block">
      <span class="brand-dot"></span>
      <p class="brand-name">Veltrano.co</p>
      <p class="brand-tagline">Polar Expeditions Specialists</p>
    </div>
    <div class="divider"></div>
    <div class="contact">
      <h1 class="person-name"><strong>Marta</strong> Delacroix</h1>
      <p class="person-title">Founder &amp; CEO</p>
      <p class="address">1840 Lindell Ave. Suite 310<br>Fairhaven, OR 97214</p>
      <ul class="details">
        <li>
          <svg viewBox="0 0 24 24" fill="none" stroke="#2d7abf" stroke-width="2.2" stroke-linecap="round" stroke-linejoin="round"><path d="M5 3h4l2 5-2.5 1.5a11 11 0 0 0 6 6L16 13l5 2v4a2 2 0 0 1-2 2A16 16 0 0 1 3 5a2 2 0 0 1 2-2z"/></svg>
          (503) 555-0147
        </li>
        <li>
          <svg viewBox="0 0 24 24" fill="none" stroke="#2d7abf" stroke-width="2.2"><circle cx="12" cy="12" r="9"/><path d="M3 12h18M12 3a14 14 0 0 1 0 18M12 3a14 14 0 0 0 0 18"/></svg>
          info@yourwebsite.com
        </li>
        <li>
          <svg viewBox="0 0 24 24" fill="none" stroke="#2d7abf" stroke-width="2.2" stroke-linejoin="round"><rect x="3" y="6" width="18" height="13" rx="1"/><path d="M3 7l9 7 9-7"/></svg>
          www.yourwebsite.com
        </li>
      </ul>
    </div>
  </section>
</body>
</html>
```